Automotive eCommerce Business looking for a business card design

Looking for a clean and simple business card design. Our company name is "Brindle Auto" and we are a company specializing in the ecommerce sales of automotive parts, specifically for pick up trucks and large SUVs. Our company colours are red, black, and white.

Feel free to use the logo provided or create a new logo that you seem fit. Looking forward to your creative ideas!

Industry/Entity Type

Automotive

Contact Information for Business Card

We were thinking of a possibly two-sided design featuring just the logo and company name on one side, and personal information on the other side. Single sided designs will be considered as well.

Font styles to use
Serif
Sans Serif
Decorative

Colors
ec1f27
ffffff
000000

Requirements
Must have
• Space for employee's name, title, phone number and email address, along with the company address and website somewhere.

```html
<!DOCTYPE html>
<html lang="en">
<head>
<meta charset="utf-8">
<title>Brindle Auto Ltd – Business Card</title>
<link rel="stylesheet" href="https://fonts.googleapis.com/css2?family=Jost:wght@400;500&family=Open+Sans:wght@400;600&display=swap">
<style>
  :root {
    --brand-red: #ec1f27;
    --ink: #000000;
    --paper: #ffffff;
    --backdrop: #e6e6e6;
    --muted: #333333;
  }
  * { box-sizing: border-box; margin: 0; padding: 0; }
  html, body { width: 1200px; height: 900px; overflow: hidden; }
  body {
    background: var(--backdrop);
    position: relative;
    font-family: "Open Sans", Arial, sans-serif;
  }
  .card {
    position: absolute;
    left: 250px;
    width: 700px;
    height: 400px;
    overflow: hidden;
    box-shadow: 0 6px 18px rgba(0,0,0,0.18);
  }
  .card--back { top: 40px; background: var(--ink); }
  .card--front { top: 460px; background: var(--paper); }

  .brand {
    position: absolute;
    display: flex;
    flex-direction: column;
    align-items: center;
    gap: 18px;
  }
  .brand__square {
    width: 84px;
    height: 84px;
    background: var(--brand-red);
  }
  .brand__name {
    font-family: "Jost", "Futura", sans-serif;
    font-weight: 500;
    font-size: 30px;
    letter-spacing: 1px;
    white-space: nowrap;
  }
  .card--back .brand { left: 50%; top: 120px; transform: translateX(-50%); }
  .card--back .brand__name { color: var(--paper); }
  .card--front .brand { right: 60px; top: 48px; gap: 14px; }
  .card--front .brand__square { width: 76px; height: 76px; }
  .card--front .brand__name { color: var(--ink); font-size: 28px; }

  .edge-bar {
    position: absolute;
    left: 0;
    top: 40px;
    width: 8px;
    height: 110px;
    background: var(--ink);
  }
  .person { position: absolute; left: 48px; top: 62px; }
  .person__name {
    font-family: "Jost", "Futura", sans-serif;
    font-weight: 500;
    font-size: 27px;
    letter-spacing: 1px;
    color: var(--brand-red);
    text-transform: uppercase;
  }
  .person__title {
    font-size: 15px;
    color: var(--muted);
    margin-top: 2px;
  }
  .divider {
    position: absolute;
    left: 290px;
    right: 60px;
    top: 212px;
    height: 2px;
    background: var(--ink);
  }
  .contacts {
    position: absolute;
    left: 48px;
    top: 150px;
    list-style: none;
  }
  .contacts li {
    display: flex;
    align-items: center;
    gap: 10px;
    font-size: 15px;
    line-height: 26px;
    color: var(--muted);
  }
  .contacts svg { width: 12px; height: 12px; flex: none; }
  .contacts .accent { color: var(--brand-red); }
</style>
</head>
<body>
  <section class="card card--back" aria-label="Card back">
    <div class="brand">
      <div class="brand__square"></div>
      <div class="brand__name">Brindle Auto Ltd</div>
    </div>
  </section>

  <section class="card card--front" aria-label="Card front">
    <div class="edge-bar"></div>
    <div class="person">
      <h1 class="person__name">Marcus Hale</h1>
      <p class="person__title">Director</p>
    </div>
    <ul class="contacts">
      <li>
        <svg viewBox="0 0 12 12" aria-hidden="true"><path d="M3 1 L5 3.5 L4 5 Q5.5 7 7 8 L8.5 7 L11 9 L9.5 11 Q5 10.5 1 3 Z" fill="#ec1f27"/></svg>
        555.240.1187
      </li>
      <li>
        <svg viewBox="0 0 12 12" aria-hidden="true"><rect x="3" y="1" width="6" height="10" rx="1" fill="none" stroke="#ec1f27" stroke-width="1.3"/><circle cx="6" cy="9" r="0.8" fill="#ec1f27"/></svg>
        555.318.6402
      </li>
      <li>
        <svg viewBox="0 0 12 12" aria-hidden="true"><rect x="1" y="2.5" width="10" height="7" fill="none" stroke="#ec1f27" stroke-width="1.3"/><path d="M1 2.5 L6 6.5 L11 2.5" fill="none" stroke="#ec1f27" stroke-width="1.3"/></svg>
        info@brindleautoltd.com
      </li>
      <li>
        <svg viewBox="0 0 12 12" aria-hidden="true"><circle cx="6" cy="6" r="5" fill="none" stroke="#ec1f27" stroke-width="1.2"/><ellipse cx="6" cy="6" rx="2" ry="5" fill="none" stroke="#ec1f27" stroke-width="1"/><line x1="1" y1="6" x2="11" y2="6" stroke="#ec1f27" stroke-width="1"/></svg>
        <span>www.<span class="accent">brindleautoltd</span>.com</span>
      </li>
    </ul>
    <div class="brand">
      <div class="brand__square"></div>
      <div class="brand__name">Brindle Auto Ltd</div>
    </div>
    <div class="divider"></div>
  </section>
</body>
</html>
```